Probate (Legal) Wordpress Design with Coding for Online Company

I need a Wordpress design with coding, pictures, content to be provided by me, fully responsive, and development. This is for a 6-7 page design.

Pages Needed: Home/About/Probate/Process/FAQ/Contact Us/Blog.

The home page should be organized as followed:
-Steps in Probate: Gather; Implement; Close (each step will come with content)
-Flat-Fee Price & Savings: Content will go here with a button to contact us (phone number) or just the phone number.
-You Have Questions, We Have Answers: five questions with content. Only one question answer to show at a time when clicked on the question from the list.
-Get to Know Us: a brief description with content about what we do and who we are.

Main image slogan: Helping Californians deal with loss with DIGNITY & UNDERSTATING (you may use a better slogan if you wish).

The Contact page should not have a map since we are an online company. We service the entire state of California in every county and city.

The About page should be simple, direct, and easy on the eye. It should have a brief description of who we are and it should have no more than 6 reasons why the client should hire us.

About our online California company. We are not attorneys but legal document assistants who prepare legal documents for probate estate when someone dies with or without a will and assets need to be distributed. We have a flat-fee for Formal Probate of $999 and $699 for Informal Probate. We are an online company and offer our services to the entire state of California in every county. We do everything over the phone and email. The turn around time for us to prepare the initial legal paperwork for the client is within 3-5 business days. We can prepare, file, serve and manage a probate matter from petition to closing. We are not attorneys so our prices are very affordable compare to the attorney.

The The Velmar Hollow Group for the website will be www.velmarhollow.com, The Velmar Hollow Group.

I do not have a logo yet. The colors of the website should be easy on the eye and calming. THE SITE SHOULD BE SIMPLE AND STRAIGHT TO THE POINT. EASY TO NAVIGATE.

The company phone number should be very visible and should stand out to the client. It should also be clickable and ready to dial for smartphone users.

I do not want a contact form on the homepage. THE MAIN THING IS FOR THE POTENTIAL CLIENT TO CALL OUR OFFICE TO SIGN UP.

I do like some images of family or people since we are dealing with people who just lost a loved one. Not all the images have to be of people.

The site should not look like we practice law or that people can mistake us for attorneys.

Target Market(s)

People who just lost a loved one who had property, assets, in California but died with or without a will or trust. This is for people looking to hire non-attorneys.

Coding

Coded - Design and coding required

Font styles to use
Serif

Colors

Designer to choose colors to be used in the design.

Requirements
Must have
• Refer to Project Description.
Nice to have
• The sample images provided is what I am attracted to for the homepage image.
Should not have

```html
<!DOCTYPE html>
<html lang="en">
<head>
<meta charset="utf-8">
<title>The Velmar Hollow Group – Home</title>
<link rel="stylesheet" href="https://fonts.googleapis.com/css2?family=Lato:wght@400;700&family=Open+Sans:wght@400;600&display=swap">
<style>
:root{
  --brand:#1565b0;
  --brand-bright:#1b8be0;
  --brand-pale:#dcebf8;
  --ink:#2b2b2b;
  --muted:#6f6f6f;
  --rule:#d9d9d9;
  --white:#ffffff;
  --band-start:#2b93e6;
  --band-end:#1849a0;
  --footer:#0a6bc4;
  --footer-bar:#1577d0;
  --soft:#ececec;
}
*{margin:0;padding:0;box-sizing:border-box}
html,body{width:1200px;height:2946px;overflow:hidden}
body{font-family:"Open Sans",Arial,sans-serif;color:var(--ink);background:var(--white);position:relative}
h1,h2,h3,h4{font-family:"Lato",Arial,sans-serif;font-weight:400}

/* header */
.site-header{position:absolute;top:0;left:0;width:1200px;height:100px;background:var(--white)}
.brand-name{position:absolute;left:114px;top:30px;font-family:"Lato",sans-serif;font-weight:700;font-size:32px;color:var(--brand);white-space:nowrap}
.main-nav a{position:absolute;top:40px;font-family:"Lato",sans-serif;font-size:15px;color:#666;text-decoration:none;white-space:nowrap}
.main-nav a.current{color:var(--brand-bright)}
.header-phone{position:absolute;left:925px;top:36px;font-family:"Lato",sans-serif;font-weight:700;font-size:19px;color:var(--brand);text-decoration:none;display:flex;align-items:center;gap:8px;white-space:nowrap}

/* hero */
.hero{position:absolute;top:100px;left:0;width:1200px;height:519px;background:linear-gradient(120deg,#7f9a4a 0%,#a9b86c 35%,#c9c39a 55%,#8e9c55 80%,#5d7630 100%)}
.hero-lead{position:absolute;left:124px;top:150px;font-family:"Lato",sans-serif;font-size:31px;line-height:40px;color:var(--white);white-space:nowrap}
.hero-strong{position:absolute;left:118px;top:240px;width:474px;border-top:2px solid var(--white);border-bottom:2px solid var(--white);padding:12px 4px 12px;font-family:"Lato",sans-serif;font-weight:700;font-size:33px;line-height:40px;color:var(--white);white-space:nowrap}
.hero-dots{position:absolute;left:558px;top:475px;display:flex;gap:10px}
.hero-dots span{width:14px;height:14px;border-radius:50%;background:var(--white)}
.hero-dots span.hollow{background:transparent;border:2px solid var(--white)}

/* steps */
.steps{position:absolute;top:619px;left:0;width:1200px;height:444px}
.section-title{position:absolute;left:0;width:1200px;text-align:center;font-family:"Lato",sans-serif;font-size:30px;color:var(--ink);white-space:nowrap}
.step{position:absolute;top:124px;width:300px;text-align:center}
.step-icon{display:block;width:84px;height:84px;margin:0 auto;border-radius:50%;background:radial-gradient(circle at 50% 45%,var(--brand-pale) 0%,#c4ddf3 100%)}
.step h3{margin-top:28px;font-size:28px;color:var(--brand);font-weight:700}
.step h3::after{content:"";display:block;width:44px;height:3px;background:var(--brand-bright);margin:10px auto 0}
.step p{margin-top:22px;font-size:14px;line-height:25px;color:var(--muted)}
.step-arrow{position:absolute;top:172px}

/* flat fee */
.fee{position:absolute;top:1063px;left:0;width:1200px;height:475px;background:linear-gradient(90deg,var(--band-start) 0%,#2280d6 45%,var(--band-end) 100%);overflow:hidden}
.fee-photo{position:absolute;right:0;top:0;width:700px;height:475px;background:linear-gradient(90deg,rgba(43,147,230,0) 0%,rgba(60,140,210,.55) 35%,rgba(24,73,160,.7) 100%)}
.fee h2{position:absolute;left:122px;top:98px;font-size:31px;color:var(--white);white-space:nowrap}
.fee p{position:absolute;left:122px;width:490px;font-size:13.5px;line-height:24px;color:var(--white)}
.btn-outline{position:absolute;left:122px;top:317px;width:165px;height:39px;border:2px solid var(--white);color:var(--white);font-family:"Lato",sans-serif;font-size:17px;display:flex;align-items:center;justify-content:center;text-decoration:none}

/* faq */
.faq{position:absolute;top:1538px;left:0;width:1200px;height:446px}
.faq .section-title{color:var(--brand);font-weight:700;top:50px;font-size:32px}
.faq-list{position:absolute;left:122px;top:136px;width:306px;list-style:none}
.faq-list li{height:37px;line-height:36px;border-bottom:1px solid var(--rule);font-size:13.5px;color:var(--ink);white-space:nowrap}
.faq-list li.active{color:var(--brand)}
.faq-list li:last-child{border-bottom:none}
.faq-answer{position:absolute;left:463px;top:128px;width:380px}
.faq-answer h3{font-size:21px;color:var(--ink);white-space:nowrap}
.faq-answer p{margin-top:14px;font-size:13px;line-height:24px;color:var(--muted)}
.faq-frame{position:absolute;left:860px;top:151px;width:195px;height:212px;background:var(--brand-bright)}
.faq-photo{position:absolute;left:890px;top:132px;width:194px;height:192px;background:linear-gradient(135deg,#9aa6ad,#d6d2cc 50%,#7f8b92)}

/* about */
.about{position:absolute;top:1984px;left:0;width:1200px;height:536px;background:linear-gradient(90deg,#f2f2f2 0%,var(--soft) 100%);overflow:hidden}
.about-photo{position:absolute;left:0;top:0;width:600px;height:536px;background:linear-gradient(90deg,#5f8e9e 0%,#9db8bf 45%,rgba(236,236,236,0) 100%)}
.about .section-title{top:42px;font-size:31px}
.about h3{position:absolute;left:601px;font-size:23px;color:var(--brand-bright);white-space:nowrap}
.about p{position:absolute;left:601px;width:490px;font-size:13px;line-height:24px;color:var(--muted)}

/* footer */
.site-footer{position:absolute;top:2520px;left:0;width:1200px;height:357px;background:linear-gradient(180deg,var(--footer) 0%,#0f74cc 100%)}
.footer-col{position:absolute;top:84px}
.footer-col h4{font-family:"Lato",sans-serif;font-weight:700;font-size:17px;color:var(--white);letter-spacing:.5px;white-space:nowrap}
.footer-col ul{list-style:none;margin-top:16px}
.footer-col li{font-size:13px;color:#dceafa;height:30px;display:flex;align-items:flex-start;gap:10px;white-space:nowrap}
.social{display:flex;gap:8px;margin-top:16px}
.social span{width:43px;height:43px;border:2px solid var(--white);border-radius:50%}
.footer-bar{position:absolute;top:2877px;left:0;width:1200px;height:69px;background:var(--footer-bar);text-align:center;line-height:69px;font-size:13px;color:#bcd8f5}
</style>
</head>
<body>

<header class="site-header">
  <div class="brand-name">Velmar Hollow</div>
  <nav class="main-nav">
    <a class="current" href="#" style="left:385px">Home</a>
    <a href="#" style="left:455px">About</a>
    <a href="#" style="left:526px">Probate</a>
    <a href="#" style="left:610px">Process</a>
    <a href="#" style="left:691px">FAQ</a>
    <a href="#" style="left:750px">Contact Us</a>
    <a href="#" style="left:855px">Blog</a>
  </nav>
  <a class="header-phone" href="tel:4155550182">
    <svg width="18" height="18" viewBox="0 0 24 24"><path d="M6.6 10.8a15 15 0 0 0 6.6 6.6l2.2-2.2c.3-.3.7-.4 1-.2 1.1.4 2.3.6 3.6.6.6 0 1 .4 1 1V20c0 .6-.4 1-1 1A17 17 0 0 1 3 4c0-.6.4-1 1-1h3.5c.6 0 1 .4 1 1 0 1.3.2 2.5.6 3.6.1.3 0 .7-.2 1z" fill="currentColor"/></svg>
    (415) 555 0182
  </a>
</header>

<section class="hero" role="img" aria-label="Photo of a smiling family in a sunny park, father lifting a small child while the mother looks up">
  <h1 class="hero-lead">Helping Californians deal<br>with loss with</h1>
  <div class="hero-strong">DIGNITY &amp; UNDERSTATING</div>
  <div class="hero-dots"><span class="hollow"></span><span></span><span></span><span></span></div>
</section>

<section class="steps">
  <h2 class="section-title" style="top:58px">Steps in Probate</h2>

  <div class="step" style="left:107px">
    <span class="step-icon" role="img" aria-label="Line icon for gathering estate information"></span>
    <h3>Gather</h3>
    <p>Donec dictum lectus non odio Cras a ante vitae enim iaculis aliquam Mauris nunc quam venenatis nec euismod sit</p>
  </div>
  <svg class="step-arrow" style="left:360px" width="130" height="40" viewBox="0 0 130 40" fill="none" stroke="#999" stroke-width="2"><path d="M4 34C40 0 90 0 120 22" stroke-dasharray="3 4"/><path d="M112 14l10 9-13 3"/></svg>

  <div class="step" style="left:445px">
    <span class="step-icon" role="img" aria-label="Line icon for carrying out the probate work"></span>
    <h3>Implement</h3>
    <p>Donec dictum lectus non odio Cras a ante vitae enim iaculis aliquam Mauris nunc quam venenatis nec euismod sit</p>
  </div>
  <svg class="step-arrow" style="left:696px" width="130" height="40" viewBox="0 0 130 40" fill="none" stroke="#999" stroke-width="2"><path d="M4 34C40 0 90 0 120 22" stroke-dasharray="3 4"/><path d="M112 14l10 9-13 3"/></svg>

  <div class="step" style="left:781px">
    <span class="step-icon" role="img" aria-label="Line icon for closing the estate"></span>
    <h3>Close</h3>
    <p>Donec dictum lectus non odio Cras a ante vitae enim iaculis aliquam Mauris nunc quam venenatis nec euismod sit</p>
  </div>
</section>

<section class="fee">
  <div class="fee-photo" role="img" aria-label="Silhouette of a woman sitting on a swing by the sea, tinted blue"></div>
  <h2>Flat-Fee Price &amp; Savings</h2>
  <p style="top:152px">Vivamus porttitor purus nisi eleifend libero a tempus libero lectus feugiat felis Morbi diam mauris viverra in gravida eu mattis in ante</p>
  <p style="top:222px">nonummy nibh ligula pulvinar metus eget consectetuer augue nisi quis lacus Ut ac mi quis lacus mollis aliquam Curabitur iaculis tempus eros Curabitur vel mi sit amet magna malesuada ultrice</p>
  <a class="btn-outline" href="tel:4155550182">Contact Us</a>
</section>

<section class="faq">
  <h2 class="section-title">You Have Questions</h2>
  <ul class="faq-list">
    <li class="active">Mauris vel lacus vitae felis vestibulum ?</li>
    <li>Volutpat Etiam est nunc venenatis ?</li>
    <li>An tristique eu imperdiet ac nisl Cum sociis ?</li>
    <li>Satoque penatibus et magnis ?</li>
    <li>Dis parturient montes nascetur ridiculus mus ?</li>
  </ul>
  <div class="faq-answer">
    <h3>Mauris vel lacus vitae felis vestibulum ?</h3>
    <p>Morbi porta libero id ullamcorper nonummy nibh ligula pulvinar metus eget consectetuer augue nisi quis lacus Ut ac mi quis lacus mollis aliquam Curabitur iaculis tempus eros Curabitur vel mi sit amet magna malesuada</p>
    <p style="margin-top:10px">Altrices Ut nisi erat fermentum vel congue id euismod in elit Fusce ultricies orci ac feugiat suscipit leo</p>
  </div>
  <div class="faq-frame"></div>
  <div class="faq-photo" role="img" aria-label="Photo of a thoughtful woman looking out of a window"></div>
</section>

<section class="about">
  <div class="about-photo" role="img" aria-label="Photo of a grieving woman sitting by the sea with her hand on her head"></div>
  <h2 class="section-title">Get to Know Us</h2>
  <h3 style="top:122px">What we do</h3>
  <p style="top:160px">Morbi porta libero id ullamcorper nonummy nibh ligula pulvinar metus eget consectetuer augue nisi quis lacus Ut ac mi quis lacus mollis aliquam Curabitur iaculis tempus eros Curabitur vel mi sit amet magna malesuada Altrices Ut nisi erat fermentum vel congue id euismod in elit Fusce ultricies orci</p>
  <h3 style="top:290px">Who we are</h3>
  <p style="top:328px">Morbi porta libero id ullamcorper nonummy nibh ligula pulvinar metus eget consectetuer augue nisi quis lacus Ut ac mi quis lacus mollis aliquam Curabitur iaculis tempus eros Curabitur vel mi sit amet magna</p>
  <p style="top:407px">malesuada Altrices Ut nisi erat fermentum vel congue id euismod in elit Fusce ultricies orciorbi diam mauris viverra in gravida eu mattis i</p>
</section>

<footer class="site-footer">
  <div class="footer-col" style="left:122px">
    <h4>CONTACT US</h4>
    <ul>
      <li><svg width="12" height="16" viewBox="0 0 12 16"><path d="M6 0a6 6 0 0 0-6 6c0 4.5 6 10 6 10s6-5.5 6-10a6 6 0 0 0-6-6zm0 8.5A2.5 2.5 0 1 1 6 3.5a2.5 2.5 0 0 1 0 5z" fill="#fff"/></svg>2740 Linden Court</li>
      <li style="padding-left:22px">Sacramento, California 95814</li>
      <li><svg width="16" height="16" viewBox="0 0 24 24" fill="none" stroke="#fff" stroke-width="2"><path d="M6.6 10.8a15 15 0 0 0 6.6 6.6l2.2-2.2c.3-.3.7-.4 1-.2 1.1.4 2.3.6 3.6.6.6 0 1 .4 1 1V20c0 .6-.4 1-1 1A17 17 0 0 1 3 4c0-.6.4-1 1-1h3.5c.6 0 1 .4 1 1 0 1.3.2 2.5.6 3.6.1.3 0 .7-.2 1z"/></svg>(916) 555-0147</li>
      <li><svg width="16" height="14" viewBox="0 0 16 12" fill="none" stroke="#fff" stroke-width="1.4"><rect x="1" y="1" width="14" height="10"/><path d="M1 1l7 6 7-6"/></svg>hello@velmarhollow.com</li>
    </ul>
  </div>
  <div class="footer-col" style="left:371px">
    <h4>COMPANY</h4>
    <ul><li>Home</li><li>About</li><li>Probate</li><li>Process</li></ul>
  </div>
  <div class="footer-col" style="left:550px">
    <h4>RESOURCES</h4>
    <ul><li>FAQ</li><li>Contact Us</li><li>Blog</li></ul>
  </div>
  <div class="footer-col" style="left:760px">
    <h4>FOLLOW US</h4>
    <div class="social" aria-label="Social links"><span></span><span></span><span></span><span></span></div>
  </div>
</footer>
<div class="footer-bar">© 2017 The Velmar Hollow Group &nbsp;All right reserved</div>

</body>
</html>
```